Business Card Design (NEW FILES)

ATTENTION: New vector files are available. Please update your design to reflect/use the new (better resolution) logo images.

Seeking a unique and professional business card design for a commercial drone photography/videography business. The layout should feature
the logo (attached) and include the following information:
Owen Tarrick
614-502-7738
www.skylarkreelworks.example
NRD Certified Remote Pilot

Owen Tarrick

```html
<!DOCTYPE html>
<html lang="en">
<head>
<meta charset="utf-8">
<title>Skylark Reelworks – Business Card</title>
<link rel="stylesheet" href="https://fonts.googleapis.com/css2?family=Open+Sans:wght@400;600;700&display=swap">
<style>
  :root {
    --page: #d8cebd;
    --card: #e8dfcf;
    --navy: #1d2550;
    --navy-deep: #151b3d;
    --orange: #d9773a;
    --ink: #1b1f33;
    --footer-text: #e3d8c6;
  }
  * { box-sizing: border-box; margin: 0; padding: 0; }
  html, body {
    width: 1200px; height: 1046px; overflow: hidden;
    background: var(--page);
    font-family: "Open Sans", Arial, sans-serif;
  }
  .card {
    position: absolute; left: 100px; top: 250px;
    width: 1000px; height: 546px;
    background: var(--card);
    overflow: hidden;
    box-shadow: 0 10px 30px rgba(60, 45, 25, 0.18);
  }
  .card-shapes { position: absolute; inset: 0; }
  .brand {
    position: absolute; left: 0; right: 0; top: 80px;
    display: flex; justify-content: center; align-items: center; gap: 14px;
  }
  .brand-dot {
    width: 30px; height: 30px; border-radius: 50%;
    background: var(--orange);
  }
  .brand-name {
    font-weight: 600; font-size: 44px; letter-spacing: 1px;
    color: var(--navy); line-height: 1;
  }
  .identity {
    position: absolute; right: 558px; top: 304px; text-align: right;
  }
  .person-name {
    font-weight: 700; font-size: 43px; line-height: 1; color: var(--navy);
  }
  .person-name .first { color: var(--orange); }
  .person-role {
    font-weight: 600; font-size: 23px; color: var(--navy); margin-top: 4px;
  }
  .divider {
    position: absolute; left: 498px; top: 283px;
    width: 3px; height: 120px; background: var(--ink);
  }
  .contact {
    position: absolute; left: 540px; top: 296px;
    list-style: none;
  }
  .contact li {
    display: flex; align-items: center; gap: 12px;
    font-weight: 600; font-size: 23px; color: var(--ink);
    height: 32px; white-space: nowrap;
  }
  .contact svg { width: 20px; height: 20px; flex: none; }
  .credentials {
    position: absolute; left: 0; right: 0; top: 454px;
    text-align: center; color: var(--footer-text);
    font-size: 25px; line-height: 31px; font-weight: 400;
  }
</style>
</head>
<body>
  <div class="card">
    <svg class="card-shapes" viewBox="0 0 1000 546" width="1000" height="546" aria-hidden="true">
      <defs>
        <linearGradient id="band" x1="0" y1="0" x2="1" y2="0">
          <stop offset="0" stop-color="#262c52"/>
          <stop offset="0.5" stop-color="#1d2550"/>
          <stop offset="1" stop-color="#121838"/>
        </linearGradient>
      </defs>
      <path d="M0 357 Q500 530 1000 357 L1000 546 L0 546 Z" fill="url(#band)"/>
      <path d="M32 358 Q498 504 964 358" fill="none" stroke="#d9773a" stroke-width="5" stroke-linecap="round"/>
    </svg>

    <div class="brand">
      <span class="brand-dot"></span>
      <span class="brand-name">SKYLARK REELWORKS</span>
    </div>

    <div class="identity">
      <p class="person-name"><span class="first">Owen</span> Tarrick</p>
      <p class="person-role">Owner</p>
    </div>

    <div class="divider"></div>

    <ul class="contact">
      <li>
        <svg viewBox="0 0 24 24" aria-hidden="true"><path fill="#d9773a" d="M6.6 10.8a15.1 15.1 0 0 0 6.6 6.6l2.2-2.2a1 1 0 0 1 1-.25 11.4 11.4 0 0 0 3.6.57 1 1 0 0 1 1 1V20a1 1 0 0 1-1 1A17 17 0 0 1 3 4a1 1 0 0 1 1-1h3.5a1 1 0 0 1 1 1c0 1.25.2 2.45.57 3.57a1 1 0 0 1-.25 1z"/></svg>
        614-502-7738
      </li>
      <li>
        <svg viewBox="0 0 24 24" aria-hidden="true"><circle cx="12" cy="12" r="10" fill="#d9773a"/><path d="M12 2a10 10 0 0 1 0 20M2 12h20M12 2c-3 3-3 17 0 20" fill="none" stroke="#e8dfcf" stroke-width="1.4"/></svg>
        www.skylarkreelworks.example
      </li>
    </ul>

    <div class="credentials">
      <p>NRD Certified Remote Pilot</p>
      <p>Fully Insured</p>
    </div>
  </div>
</body>
</html>
```